Book Cover: Quiet Harbor: Small Ceremonies For The Restless Soul

I would like a full cover spread- front, back and spine as well as a stand alone front cover for Kindle for the book. Design a cover that mirrors the profound depth and dynamic energy of 'Quiet Harbor.' Envision a visual tapestry that draws readers into a transformative journey, where spirituality and self-care unite. Explore vibrant colors, intricate textures, and a sense of inner radiance that beckons readers to explore the book's rich wisdom within. See images for design inspiration attached. Even though some of the images are cartoon, I'd like the cover to be more serious than playful and very elegant.

About this book (back cover copy)
Are you ready to embark on a transformative journey and elevate your daily existence? "Quiet Harbor" is a treasure trove of practical yet profound rituals and wisdom from renowned self-care, healing, and spirituality experts.

Within these pages, you'll uncover a tapestry of guidance and insight from some of the world's most respected mentors. Their collective wisdom is your key to creating a sacred sanctuary within your everyday life.

From invigorating morning rituals to meditative practices, empowering affirmations, and transformative energy healing, you'll find a rich tapestry of tools to nurture a deeper connection with yourself and the universe.

Whether you're a seasoned practitioner or a newcomer to the world of self-care and spirituality, "Quiet Harbor" is your trusted companion on the journey to transform your life and elevate your daily experience. Open this book today and start your sacred, fulfilling adventure.

Colors
0094D4
00A9DD
6FCCEA
C7EBF8
E9F6FB
E54698
E96AAD
F1A4CE
F9D9EA
FCEFF6
6B429C
8869AF
B7A5CE
E3DAEB
F3F0F8

Requirements
Must have
• Title: Quiet Harbor: Subtitle: Small Ceremonies For The Restless Soul Name of Publisher: Lantern Bough Publishing- Logo on the back Back cover copy

```html
<!DOCTYPE html>
<html lang="en">
<head>
<meta charset="utf-8">
<title>Quiet Harbor — Cover Spread</title>
<link rel="stylesheet" href="https://fonts.googleapis.com/css2?family=Allura&family=Crimson+Pro:ital,wght@0,400;0,600;1,400&family=Josefin+Sans:wght@300;400&family=Marcellus&family=Roboto:wght@300;700&display=swap">
<style>
  :root {
    --stage: #000000;
    --paper: #fdfdfc;
    --teal: #1f5a63;
    --teal-deep: #174a52;
    --ink: #1a1a1a;
    --gold-light: #f3d77a;
    --gold: #c9a043;
    --gold-deep: #a9822e;
    --leaf-deep: rgba(47,120,120,0.75);
    --leaf-mid: rgba(111,167,165,0.6);
    --leaf-soft: rgba(207,227,226,0.8);
    --sage-soft: rgba(190,215,205,0.65);
    --blossom: rgba(241,164,206,0.8);
    --blossom-soft: rgba(249,217,234,0.85);
    --clear: rgba(255,255,255,0);
    --barcode-box: #efefef;
  }
  * { box-sizing: border-box; margin: 0; padding: 0; }
  html, body {
    width: 1200px; height: 1200px; overflow: hidden;
    background: var(--stage);
  }
  .spread {
    position: absolute; left: 14px; top: 184px;
    width: 1171px; height: 832px;
    background: var(--paper);
    overflow: hidden;
  }

  /* Watercolour areas: every gradient fades to clear inside its own box */
  .art { position: absolute; pointer-events: none; }
  .art--back-blossom {
    left: -90px; top: 10px; width: 250px; height: 230px;
    background: radial-gradient(closest-side, var(--blossom-soft) 0%, rgba(249,217,234,0.45) 50%, var(--clear) 100%);
  }
  .art--back-top-leaves {
    left: 100px; top: -90px; width: 360px; height: 220px;
    background: radial-gradient(closest-side, var(--leaf-soft) 0%, rgba(207,227,226,0.35) 55%, var(--clear) 100%);
  }
  .art--back-leaves {
    left: -120px; top: 420px; width: 360px; height: 500px;
    background: radial-gradient(closest-side, var(--leaf-mid) 0%, rgba(150,196,192,0.35) 55%, var(--clear) 100%);
  }
  .art--spine-leaves {
    left: 500px; top: 20px; width: 300px; height: 260px;
    background: radial-gradient(closest-side, rgba(207,227,226,0.6) 0%, var(--clear) 100%);
  }
  .art--front-leaves {
    left: 720px; top: -120px; width: 420px; height: 520px;
    background: radial-gradient(closest-side, var(--leaf-deep) 0%, rgba(111,167,165,0.4) 50%, var(--clear) 100%);
  }
  .art--front-blossoms {
    left: 930px; top: -80px; width: 320px; height: 400px;
    background: radial-gradient(closest-side, var(--blossom) 0%, rgba(241,164,206,0.35) 55%, var(--clear) 100%);
  }
  .art--front-sprigs {
    left: 980px; top: 560px; width: 260px; height: 330px;
    background: radial-gradient(closest-side, var(--sage-soft) 0%, var(--clear) 100%);
  }
  .art--front-bottom {
    left: 640px; top: 720px; width: 320px; height: 200px;
    background: radial-gradient(closest-side, var(--blossom-soft) 0%, rgba(207,227,226,0.35) 55%, var(--clear) 100%);
  }

  .script {
    font-family: "Allura", cursive;
    font-weight: 400;
    background: linear-gradient(100deg, var(--gold-light) 0%, var(--gold) 45%, var(--gold-deep) 75%, var(--gold-light) 100%);
    -webkit-background-clip: text; background-clip: text;
    color: transparent;
    line-height: 1.1;
    white-space: nowrap;
    padding: 0 30px 0 10px;
  }

  /* Back cover */
  .back { position: absolute; left: 0; top: 0; width: 548px; height: 832px; }
  .back__title { position: absolute; left: 150px; top: 52px; }
  .back__title-main { display: block; font-size: 96px; }
  .back__title-sub { display: block; font-size: 62px; margin: -40px 0 0 70px; }
  .back__subtitle {
    position: absolute; left: 0; width: 586px; top: 200px;
    text-align: center;
    font-family: "Marcellus", serif;
    font-size: 21px; color: var(--teal);
    white-space: nowrap;
  }
  .back__subtitle strong { color: var(--teal-deep); font-weight: 400; -webkit-text-stroke: 0.4px var(--teal-deep); }
  .connector { font-family: "Allura", cursive; font-size: 26px; }
  .back__copy {
    position: absolute; left: 80px; top: 240px; width: 426px;
    text-align: center;
    font-family: "Crimson Pro", serif;
    font-size: 15.4px; line-height: 19.3px;
    color: var(--ink);
  }
  .back__copy p + p { margin-top: 19.3px; }
  .back__copy strong { font-weight: 600; }
  .publisher {
    position: absolute; left: 176px; top: 716px; width: 180px;
    text-align: center;
    font-family: "Josefin Sans", sans-serif; color: var(--ink);
  }
  .publisher__name { display: block; font-size: 20px; font-weight: 400; white-space: nowrap; }
  .publisher__line { display: block; font-size: 16px; letter-spacing: 2.5px; margin-top: 6px; }
  .barcode-area {
    position: absolute; left: 363px; top: 705px; width: 144px; height: 86px;
    background: var(--barcode-box);
  }

  /* Spine: a horizontal strip turned to read top to bottom */
  .spine {
    position: absolute; left: 607px; top: 28px;
    width: 780px; height: 50px;
    transform-origin: top left;
    transform: rotate(90deg);
    display: flex; align-items: center;
    white-space: nowrap;
  }
  .spine__title { font-size: 54px; padding: 0 10px 0 0; margin-right: 6px; }
  .spine__subtitle {
    font-family: "Roboto", sans-serif; font-weight: 300;
    font-size: 17px; color: var(--teal);
    margin-right: 18px;
  }
  .spine__subtitle strong { font-weight: 700; }
  .spine .connector { font-size: 21px; }
  .spine__publisher {
    font-family: "Roboto", sans-serif; font-weight: 300;
    font-size: 17px; color: var(--teal);
  }
  .spine__publisher strong { font-weight: 700; }

  /* Front cover */
  .front { position: absolute; left: 613px; top: 0; width: 558px; height: 832px; }
  .front__title { position: absolute; left: 20px; top: 318px; }
  .front__title-main { display: block; font-size: 200px; }
  .front__title-sub { display: block; font-size: 120px; margin: -92px 0 0 120px; }
  .front__subtitle {
    position: absolute; left: 0; width: 470px; top: 642px;
    text-align: center;
    font-family: "Marcellus", serif; color: var(--teal);
    line-height: 1;
  }
  .front__subtitle-line { display: block; font-size: 33px; white-space: nowrap; }
  .front__subtitle-line--bold { color: var(--teal-deep); -webkit-text-stroke: 0.6px var(--teal-deep); }
  .front__subtitle .connector { display: block; font-size: 36px; margin: -2px 0 -4px; }
</style>
</head>
<body>
  <main class="spread">
    <div class="art art--back-blossom" role="img" aria-label="Soft watercolor pink blossom at the top left edge"></div>
    <div class="art art--back-top-leaves" role="img" aria-label="Pale watercolor leaves along the top edge"></div>
    <div class="art art--back-leaves" role="img" aria-label="Watercolor teal and green leaves in the lower left corner"></div>
    <div class="art art--spine-leaves" role="img" aria-label="Faint watercolor leaves across the spine"></div>
    <div class="art art--front-leaves" role="img" aria-label="Watercolor teal leaves in the top right corner"></div>
    <div class="art art--front-blossoms" role="img" aria-label="Watercolor pink blossoms in the top right corner"></div>
    <div class="art art--front-sprigs" role="img" aria-label="Pale sage eucalyptus sprigs at the lower right"></div>
    <div class="art art--front-bottom" role="img" aria-label="Faint pink blossom and pale leaves along the bottom edge"></div>

    <section class="back">
      <h2 class="back__title script">
        <span class="back__title-main">Quiet</span>
        <span class="back__title-sub">Harbor</span>
      </h2>
      <p class="back__subtitle"><strong>Small Ceremonies</strong> <span class="connector">for</span> The Restless Soul</p>
      <div class="back__copy">
        <p><strong>Are you ready to embark on a transformative journey and elevate your daily existence?</strong> <em>"Quiet Harbor"</em> is a treasure trove of practical yet profound rituals and wisdom from renowned self-care, healing, and spirituality experts.</p>
        <p>Within these pages, you'll uncover a tapestry of guidance and insight from some of the world's most respected mentors. Their collective wisdom is your key to creating a sacred sanctuary within your everyday life.</p>
        <p>From invigorating morning rituals to meditative practices, empowering affirmations, and transformative energy healing, you'll find a rich tapestry of tools to nurture a deeper connection with yourself and the universe.</p>
        <p>Whether you're a seasoned practitioner or a newcomer to the world of self-care and spirituality, "Quiet Harbor" is your trusted companion on the journey to transform your life and elevate your daily experience. Open this book today and start your sacred, fulfilling adventure.</p>
      </div>
      <div class="publisher">
        <span class="publisher__name">Lantern Bough</span>
        <span class="publisher__line">Publishing</span>
      </div>
      <div class="barcode-area"></div>
    </section>

    <section class="spine">
      <span class="spine__title script">Quiet Harbor</span>
      <span class="spine__subtitle"><strong>Small Ceremonies</strong> <span class="connector">for</span> The Restless Soul</span>
      <span class="spine__publisher"><strong>Lantern Bough</strong> Publishing</span>
    </section>

    <section class="front">
      <h1 class="front__title script">
        <span class="front__title-main">Quiet</span>
        <span class="front__title-sub">Harbor</span>
      </h1>
      <p class="front__subtitle">
        <span class="front__subtitle-line front__subtitle-line--bold">Small Ceremonies</span>
        <span class="connector">for</span>
        <span class="front__subtitle-line">The Restless Soul</span>
      </p>
    </section>
  </main>
</body>
</html>
```